PixelHarbor Rangers (Ledgerline Nova)
A website dedicated to crypto education. We are a new company focused on blockchain edutainment (education and interesting and entertaining content about the blockchain space). We want a fun, clean/minimalist and modern website that is made up of an education platform which could be a website in it’s own right. It will be the reference point for our users/community for all of our other blockchain based content in the PHR website ecosystem which will be covering; crypto news, digital asset investing (including a technical and fundamental analysis subscription service), blockchain business solutions and an NFT section that will cover creative art projects (art, music, gaming and more). To feature a logins and payment system which may need a shopping basket set up for tutorial/educational platform that is accessed via the website, NFT page with sub-categories: education and NFT and metaverse/virtual world and merchandise shopping page which is Web 3.0 enabled (able to link to a VeloPurse, Keyhold Vault etc , digital asset education page featuring blog and newsletter subscriptions links, A social media page where people can access videos, podcasts and our presence on other platforms such as Chirplo, Snapmora, Huddlex, Wirepost etc.
Number of Pages Required
5+ page
Look and feel

```html
<!DOCTYPE html>
<html lang="en">
<head>
<meta charset="utf-8">
<title>PixelHarbor Rangers — Ledgerline Nova</title>
<link rel="stylesheet" href="https://fonts.googleapis.com/css2?family=IBM+Plex+Sans:wght@400;500;600;700&display=swap">
<style>
:root{
  --bg:#000;
  --ink:#fff;
  --muted:#c9c9c9;
  --purple:#7b2fe0;
  --blue:#3fb6ee;
  --green:#6fe23a;
  --card-line:#2b2b2b;
  --badge:#2aa7e8;
}
*{margin:0;padding:0;box-sizing:border-box}
html,body{width:1200px;height:4208px;overflow:hidden}
body{background:var(--bg);color:var(--ink);font-family:"IBM Plex Sans",Arial,sans-serif;position:relative}
.abs{position:absolute}
.art{position:absolute}

/* header */
.phone{left:680px;top:36px;font-size:19px;font-weight:600;display:flex;align-items:center;gap:8px}
.cart{left:887px;top:33px}
.login{left:942px;top:26px;width:113px;height:46px;border-radius:23px;background:var(--purple);font-size:16px;font-weight:600;display:flex;align-items:center;justify-content:center}
.brand{left:144px;top:72px;font-size:62px;font-weight:700;color:var(--purple);letter-spacing:6px;line-height:65px}
.nav{left:470px;top:94px;display:flex;gap:30px;font-size:12px;font-weight:500}
.nav a{color:var(--ink);text-decoration:none;padding-bottom:7px}
.nav a.active{border-bottom:2px solid var(--blue)}

/* hero */
.hero-bg{left:0;top:0;width:1200px;height:720px;background:radial-gradient(ellipse 70% 30% at 50% 78%,#4a4a4a 0%,#1b1b1b 45%,#000 100%)}
.hero-title{left:0;top:225px;width:1200px;text-align:center;font-size:80px;font-weight:700;line-height:90px}
.hero-title .a{color:var(--blue)}.hero-title .b{color:var(--green)}
.hero-sub{left:0;top:340px;width:1200px;text-align:center;font-size:26px;font-weight:600;line-height:33px}
.play{left:552px;top:439px}

/* generic */
h2{font-weight:700;letter-spacing:.5px}
.h-left{font-size:44px;line-height:51px}
.h-center{left:0;width:1200px;text-align:center;font-size:45px}
.body-text{font-size:13.5px;line-height:24.8px;color:var(--muted)}
.btn{height:62px;width:203px;border-radius:31px;background:var(--purple);font-size:21px;font-weight:600;display:flex;align-items:center;justify-content:center}
.arrow{width:42px;height:42px;border:2px solid #fff;border-radius:50%;display:flex;align-items:center;justify-content:center}

/* mesh bands */
.band{left:0;width:1200px;background:linear-gradient(180deg,#000 0%,#151515 50%,#000 100%)}

/* news */
.news-card{top:1577px;width:294px;height:278px;border:1px solid var(--card-line);padding:0 18px}
.date{top:-24px;left:18px;width:62px;height:65px;background:var(--badge);text-align:center;font-size:15px;font-weight:600;line-height:23px;padding-top:9px;position:absolute}
.news-card h3{margin-top:79px;font-size:15px;font-weight:600}
.news-card p{margin-top:16px;font-size:13px;line-height:22px;color:var(--muted)}
.news-card .more{margin-top:22px;font-size:15px;font-weight:700;color:var(--purple)}

/* nft */
.ring{width:226px;height:226px;border-radius:50%;border:14px solid;top:2711px}
.ring-label{top:2951px;width:226px;text-align:center;font-size:25px;font-weight:700}

/* education */
.edu h3{font-size:15px;font-weight:600}
.edu p{font-size:13px;line-height:23px;color:var(--muted);margin-top:17px;width:420px}

/* footer */
.rule{left:0;top:3826px;width:1200px;height:1px;background:#1c1c1c}
.foot-bg{left:0;top:3827px;width:1200px;height:381px;background:linear-gradient(180deg,#000 40%,#1c1c1c 100%)}
.foot-brand{left:144px;top:3912px;font-size:104px;font-weight:700;color:var(--purple);letter-spacing:10px;line-height:110px}
.pay{left:144px;top:4078px;display:flex;gap:14px;font-size:12px;font-weight:500}
.pay span{display:flex;align-items:center;gap:5px}
.pay i{width:10px;height:10px;background:#fff;display:inline-block}
.links h4{font-size:21px;font-weight:600;color:var(--blue)}
.links ul{list-style:none;margin-top:18px;font-size:13px;line-height:29px}
.wallet{font-size:17px;font-weight:500;display:flex;align-items:center;gap:9px}
.wallet i{width:28px;height:28px;display:inline-block}
.social{display:grid;grid-template-columns:140px 140px;row-gap:12px;font-size:14px}
.social span{display:flex;align-items:center;gap:8px}
.social i{width:16px;height:16px;border-radius:50%;display:inline-block}
</style>
</head>
<body>

<div class="abs hero-bg"></div>

<!-- header -->
<div class="abs brand">PHR</div>
<div class="abs phone">
  <svg width="16" height="16" viewBox="0 0 24 24"><path fill="#3fb6ee" d="M6.6 10.8a15.2 15.2 0 0 0 6.6 6.6l2.2-2.2a1 1 0 0 1 1-.25 11.4 11.4 0 0 0 3.6.57 1 1 0 0 1 1 1V20a1 1 0 0 1-1 1A17 17 0 0 1 3 4a1 1 0 0 1 1-1h3.5a1 1 0 0 1 1 1c0 1.250.2 2.450.57 3.570a1 1 0 0 1-.25 1z"/></svg>
  +1 555 014 2290
</div>
<div class="abs cart">
  <svg width="36" height="32" viewBox="0 0 36 32"><path d="M2 4h5l4 16h16l4-11H9" fill="none" stroke="#fff" stroke-width="2.2" stroke-linejoin="round"/><circle cx="13" cy="26" r="2.2" fill="#fff"/><circle cx="25" cy="26" r="2.2" fill="#fff"/><circle cx="30" cy="6" r="6" fill="#7b2fe0"/><text x="30" y="9" font-size="8" fill="#fff" text-anchor="middle" font-family="IBM Plex Sans, sans-serif">0</text></svg>
</div>
<div class="abs login">LOGIN</div>
<nav class="abs nav">
  <a class="active">HOME</a><a>CRYPTO NEWS</a><a>DIGITAL ASSET INVESTING</a><a>MERCHANDISE</a><a>NFT PROJECTS</a>
</nav>

<!-- hero -->
<h1 class="abs hero-title"><span class="a">LEDGERLINE</span> <span class="b">NOVA</span></h1>
<p class="abs hero-sub">Sed ut perspiciatis unde omnis iste natus error<br>sit voluptatem accusantium</p>
<svg class="abs play" width="98" height="98" viewBox="0 0 98 98"><circle cx="49" cy="49" r="44" fill="none" stroke="#fff" stroke-width="7"/><path d="M38 28 L70 49 L38 70 Z" fill="#fff"/></svg>

<!-- digital asset investing -->
<div class="abs band" style="top:1180px;height:300px"></div>
<h2 class="abs h-left" style="left:142px;top:782px">DIGITAL<br>ASSET INVESTING</h2>
<p class="abs" style="left:142px;top:907px;font-size:19px;font-weight:500;color:var(--blue)">Technical and fundamental analysis subscription service</p>
<p class="abs body-text" style="left:142px;top:956px;width:480px">Lorem ipsum dolor sit amet, consectetur adipiscing elit, sed do eiusmod tempor incididunt ut labore et dolore magna aliqua. Quis ipsum suspendisse ultrices gravida. Risus commodo viverra maecenas accumsan lafacilisorem ipsum dolor sit amet, consectetur adipiscing elit, sed do eiusmod tempor incididunt ut labore et dolore magna aliquis ipsum suspendisse ultrices gravidisus cviverra maecenas accumsan lacus vel facilisis.</p>
<div class="abs btn" style="left:142px;top:1156px">READ MORE</div>
<div class="art" role="img" aria-label="Pixel space invader filled with glowing crypto coin imagery" style="left:661px;top:789px;width:471px;height:432px;background:radial-gradient(ellipse at 50% 45%,#1e8fc4 0%,#0c3f7a 45%,#030a2a 80%,#000 100%)"></div>

<!-- crypto news -->
<div class="art" role="img" aria-label="Pixel tiger mascot" style="left:54px;top:1319px;width:131px;height:112px;background:linear-gradient(135deg,#f07a22,#a8410f)"></div>
<h2 class="abs h-center" style="top:1425px">CRYPTO NEWS</h2>
<div class="abs arrow" style="left:57px;top:1694px"><svg width="14" height="14" viewBox="0 0 14 14"><path d="M9 2 L4 7 L9 12" fill="none" stroke="#fff" stroke-width="2"/></svg></div>
<div class="abs arrow" style="left:1101px;top:1694px"><svg width="14" height="14" viewBox="0 0 14 14"><path d="M5 2 L10 7 L5 12" fill="none" stroke="#fff" stroke-width="2"/></svg></div>

<article class="abs news-card" style="left:144px">
  <div class="date">FEB<br>2022</div>
  <h3>NEMO ENIM IPSALUPTATEM</h3>
  <p>Lorem ipsum dolor sit amet, consectetur adipiscing elit, sed do eiusmod tempor incididunt ut labore et dolore magna aliqua ipsum suspendisse ulavi</p>
  <div class="more">READ MORE</div>
</article>
<article class="abs news-card" style="left:452px">
  <div class="date">FEB<br>2022</div>
  <h3>NEQUE PORRO QUISQUAM</h3>
  <p>Lorem ipsum dolor sit amet, consectetur adipiscing elit, sed do eiusmod tempor incididunt ut labore et dolore magna aliqua ipsum suspendisse ulavi</p>
  <div class="more">READ MORE</div>
</article>
<article class="abs news-card" style="left:761px">
  <div class="date">FEB<br>2022</div>
  <h3>QUIS AUTEM VEL EUM IURE</h3>
  <p>Lorem ipsum dolor sit amet, consectetur adipiscing elit, sed do eiusmod tempor incididunt ut labore et dolore magna aliqua ipsum suspendisse ulavi</p>
  <div class="more">READ MORE</div>
</article>

<!-- blockchain business solutions -->
<div class="art" role="img" aria-label="Pixel penguin mascot with headphones" style="left:1065px;top:1922px;width:121px;height:129px;background:linear-gradient(180deg,#2b3f8c,#e9e9e9 55%,#2f8a5a)"></div>
<div class="art" role="img" aria-label="Network of connected blue and purple cubes" style="left:36px;top:1992px;width:467px;height:433px;background:radial-gradient(ellipse at 50% 50%,#1d6a9e 0%,#30217a 45%,#000 75%)"></div>
<h2 class="abs h-left" style="left:586px;top:2020px">BLOCKCHAIN<br>BUSINESS SOLUTIONS</h2>
<p class="abs body-text" style="left:586px;top:2144px;width:480px">Lorem ipsum dolor sit amet, consectetur adipiscing elit, sed do eiusmod tempor incididunt ut labore et dolore magna aliqua. Quis ipsum suspendisse ultrices gravida. Risus commodo viverra maecenas accumsan lafacilisorem ipsum dolor sit amet, consectetur adipiscing elit, sed do eiusmod tempor incididunt ut labore et dolore magna aliquis ipsum suspendisse ultrices gravidisus cviverra maecenas accumsan lacus vel facilisis.</p>
<div class="abs btn" style="left:586px;top:2329px">READ MORE</div>

<!-- nft -->
<div class="abs band" style="top:2450px;height:160px"></div>
<h2 class="abs h-center" style="top:2580px">NFT CREATIVE ART PROJECTS</h2>
<svg class="abs" style="left:114px;top:2790px" width="36" height="66" viewBox="0 0 36 66"><path d="M33 2 L3 33 L33 64" fill="none" stroke="#555" stroke-width="2"/></svg>
<svg class="abs" style="left:1050px;top:2790px" width="36" height="66" viewBox="0 0 36 66"><path d="M3 2 L33 33 L3 64" fill="none" stroke="#555" stroke-width="2"/></svg>

<div class="abs ring" style="left:187px;border-color:var(--purple)"><div class="art" role="img" aria-label="Pixel artist character sitting" style="inset:20px;border-radius:50%;background:radial-gradient(circle,#6b5a3a,#111 70%)"></div></div>
<div class="abs ring" style="left:486px;border-color:var(--blue)"><div class="art" role="img" aria-label="Pixel character listening to music" style="inset:20px;border-radius:50%;background:radial-gradient(circle,#7a3a4e,#111 70%)"></div></div>
<div class="abs ring" style="left:787px;border-color:var(--green)"><div class="art" role="img" aria-label="Pixel red gaming robot" style="inset:20px;border-radius:50%;background:radial-gradient(circle,#8a2424,#111 70%)"></div></div>
<div class="abs ring-label" style="left:187px">ART</div>
<div class="abs ring-label" style="left:486px">MUSIC</div>
<div class="abs ring-label" style="left:787px">GAMING</div>

<!-- education -->
<h2 class="abs h-center" style="top:3151px">DIGITAL ASSET EDUCATION</h2>
<div class="abs arrow" style="left:57px;top:3372px"><svg width="14" height="14" viewBox="0 0 14 14"><path d="M9 2 L4 7 L9 12" fill="none" stroke="#fff" stroke-width="2"/></svg></div>
<div class="abs arrow" style="left:1101px;top:3372px"><svg width="14" height="14" viewBox="0 0 14 14"><path d="M5 2 L10 7 L5 12" fill="none" stroke="#fff" stroke-width="2"/></svg></div>

<div class="art" role="img" aria-label="Photo of a laptop with glowing blue trading data" style="left:144px;top:3261px;width:449px;height:265px;background:linear-gradient(120deg,#cfe3f2 0%,#3b7fc4 45%,#0b2c63 100%)"></div>
<div class="art" role="img" aria-label="Photo of a hand over a laptop with rising market chart" style="left:609px;top:3261px;width:449px;height:265px;background:linear-gradient(120deg,#b5a9a2 0%,#6e5a52 50%,#2a2220 100%)"></div>

<div class="abs edu" style="left:144px;top:3557px">
  <h3>NEMO ENIM IPSALUPTATXERCITATIONEEM</h3>
  <p>Lorem ipsum dolor sit amet, consectetur adipiscing elit, sed do eiusmod tempor incididunt ut labore et dolore magna aliqua</p>
</div>
<div class="abs edu" style="left:609px;top:3557px">
  <h3>EQUE PORRO QUISQUAM ESTQUI DOLOREM</h3>
  <p>Lorem ipsum dolor sit amet, consectetur adipiscing elit, sed do eiusmod tempor incididunt ut labore et dolore magna aliqua</p>
</div>
<div class="abs btn" style="left:144px;top:3666px">SIGN UP</div>
<div class="abs btn" style="left:609px;top:3666px">SIGN UP</div>

<!-- footer -->
<div class="abs foot-bg"></div>
<div class="abs rule"></div>
<div class="abs foot-brand">PHR</div>
<div class="abs pay">
  <span><i></i>Payvio</span><span><i></i>Cardora</span><span><i></i>Findly</span><span><i></i>Amerix Pay</span><span><i></i>Sendora</span>
</div>
<div class="abs links" style="left:541px;top:3914px">
  <h4>LINKS</h4>
  <ul><li>Home</li><li>Crypto news</li><li>Digital asset investing</li><li>Merchandise</li><li>NFT projects</li></ul>
</div>
<div class="abs wallet" style="left:777px;top:3950px"><i style="background:#f08a2b"></i>VeloPurse</div>
<div class="abs wallet" style="left:903px;top:3950px"><i style="background:#fff;border-radius:6px"></i>Keyhold Vault</div>
<div class="abs social" style="left:777px;top:4040px">
  <span><i style="background:#1d9bf0"></i>Chirplo</span>
  <span><i style="background:#d6296f"></i>Snapmora</span>
  <span><i style="background:#5865f2"></i>Huddlex</span>
  <span><i style="background:#2aa3e0"></i>Wirepost</span>
</div>

</body>
</html>
```